Business Card Design Project

Business card based on attached logo

Todd Merrick
Todd@lorvantest.com
877-514-9073 ext. 318
Www.LorvanTest.com

Industry/Entity Type

Business

```html
<!DOCTYPE html>
<html lang="en">
<head>
<meta charset="utf-8">
<title>LorvanTest Business Cards</title>
<link href="https://fonts.googleapis.com/css2?family=Arimo:wght@400;700&display=swap" rel="stylesheet">
<style>
  :root {
    --sheet: #8a8c8f;
    --paper: #ffffff;
    --ink: #231f20;
    --red: #e1252b;
    --red-deep: #c7222a;
    --tint: #fde8e8;
    --charcoal: #1f1f1f;
    --charcoal-light: #3a3a3a;
  }
  * { margin: 0; padding: 0; box-sizing: border-box; }
  html, body { width: 1200px; height: 720px; overflow: hidden; background: var(--sheet); }
  body { position: relative; font-family: "Arimo", Arial, sans-serif; }

  .card {
    position: absolute;
    width: 564px;
    height: 322px;
    overflow: hidden;
    border: 1px solid #6f7174;
  }
  .card--contact { left: 28px; top: 26px; background: var(--paper); }
  .card--red { left: 612px; top: 26px; background: linear-gradient(120deg, var(--red) 0%, var(--red-deep) 100%); }
  .card--white { left: 28px; top: 373px; background: var(--paper); }
  .card--dark { left: 612px; top: 373px; background: radial-gradient(ellipse at 50% 45%, var(--charcoal-light) 0%, var(--charcoal) 70%); }

  .wordmark {
    position: absolute;
    display: flex;
    align-items: center;
    gap: 12px;
    font-weight: 700;
    letter-spacing: -1px;
    line-height: 1;
    white-space: nowrap;
  }
  .wordmark__square { display: block; flex: none; }

  .card--contact .wordmark { left: 34px; top: 52px; font-size: 50px; color: var(--ink); }
  .card--contact .wordmark__square { width: 22px; height: 22px; background: var(--red); }

  .contact-list { position: absolute; left: 32px; top: 206px; list-style: none; }
  .contact-list li {
    display: flex; align-items: center; gap: 8px;
    height: 28px; font-size: 17px; color: var(--ink);
  }
  .contact-list svg { width: 15px; height: 15px; flex: none; }

  .accent-square {
    position: absolute; right: 0; top: 160px;
    width: 150px; height: 150px; background: var(--tint);
  }
  .holder-name {
    position: absolute; right: 24px; top: 214px;
    font-size: 19px; color: var(--red); letter-spacing: 0.3px;
  }

  .card--red .wordmark { left: 36px; top: 62px; font-size: 64px; color: var(--paper); }
  .card--red .accent-square {
    top: auto; bottom: 60px; right: 0; width: 120px; height: 120px;
    background: rgba(255,255,255,0.12); box-shadow: 0 0 0 1px rgba(0,0,0,0.08);
  }

  .web {
    position: absolute; font-size: 17px; letter-spacing: 3px;
  }
  .card--red .web { left: 36px; bottom: 16px; color: var(--paper); }

  .card--white .wordmark, .card--dark .wordmark {
    left: 0; right: 0; justify-content: center; top: 110px; font-size: 62px;
  }
  .card--white .wordmark { color: var(--ink); }
  .card--white .wordmark__square { width: 26px; height: 26px; background: var(--red); }
  .card--dark .wordmark { color: var(--paper); }
  .card--dark .wordmark__square { width: 26px; height: 26px; background: var(--paper); }

  .card--white .web, .card--dark .web { left: 0; right: 0; text-align: center; bottom: 22px; }
  .card--white .web { color: var(--ink); }
  .card--dark .web { color: var(--paper); }
</style>
</head>
<body>

  <section class="card card--contact">
    <div class="wordmark"><span>LorvanTest</span><span class="wordmark__square"></span></div>
    <ul class="contact-list">
      <li>
        <svg viewBox="0 0 16 16" aria-hidden="true"><circle cx="8" cy="8" r="7" fill="none" stroke="#e1252b" stroke-width="1.5"/><path d="M5.5 4.5c.6-.4 1.1 0 1.3.6l.3.9c.1.4 0 .7-.3.9l-.4.3c.4.9 1 1.6 1.9 2l.3-.4c.3-.3.6-.3.9-.2l.9.4c.6.3.8.8.4 1.3-.8 1-2.2 1-3.6-.1-1.2-1-2.2-2.4-2.3-3.6 0-.9.2-1.6.6-2.1z" fill="#e1252b"/></svg>
        877-514-9073 ext. 318
      </li>
      <li>
        <svg viewBox="0 0 16 16" aria-hidden="true"><rect x="1" y="4" width="14" height="9" rx="1" fill="#e1252b"/><path d="M1.5 4.5 8 9l6.5-4.5" fill="none" stroke="#fff" stroke-width="1.2"/></svg>
        Todd@lorvantest.com
      </li>
      <li>
        <svg viewBox="0 0 16 16" aria-hidden="true"><g fill="none" stroke="#e1252b" stroke-width="1.2"><circle cx="8" cy="8" r="6.5"/><ellipse cx="8" cy="8" rx="3" ry="6.5"/><path d="M1.5 8h13M2.5 5h11M2.5 11h11"/></g></svg>
        www.lorvantest.com
      </li>
    </ul>
    <span class="accent-square" aria-hidden="true"></span>
    <p class="holder-name">TODD MERRICK</p>
  </section>

  <section class="card card--red">
    <div class="wordmark"><span>LorvanTest</span></div>
    <span class="accent-square" aria-hidden="true"></span>
    <p class="web">www.lorvantest.com</p>
  </section>

  <section class="card card--white">
    <div class="wordmark"><span>LorvanTest</span><span class="wordmark__square"></span></div>
    <p class="web">www.lorvantest.com</p>
  </section>

  <section class="card card--dark">
    <div class="wordmark"><span>LorvanTest</span><span class="wordmark__square"></span></div>
    <p class="web">www.lorvantest.com</p>
  </section>

</body>
</html>
```